Corvane Holdings , new business card design

investment firm with corporate clients . need double sided business card , vertical and horizontal options ,logo must be clear. prefer pantone colors only and sharp design. website also www.corvane.ae

Khalid Bin Tarrafi
Managing Director
Tel. +971 4 387 2940
Mobile +971 50 518 2403
khalid@corvane.ae
Q-Span Plaza, officw 18-B07, Warqa Gardens, Dubai

Contact Information for Business Card

Khalid Bin Tarrafi
Managing Director

Font styles to use
Serif

Colors

Designer to choose colors to be used in the design.

```html
<!DOCTYPE html>
<html lang="en">
<head>
<meta charset="utf-8">
<title>Corvane Holdings – Business Card</title>
<link rel="stylesheet" href="https://fonts.googleapis.com/css2?family=Roboto+Condensed:wght@400;700&family=Roboto:wght@400;500&family=Josefin+Sans:wght@300&display=swap">
<style>
  :root {
    --backdrop: #2b2b2e;
    --card: #1d1d1f;
    --ink: #f2f2f2;
    --accent: #4f8cc4;
    --rule: #6a6a6e;
  }
  * { box-sizing: border-box; margin: 0; padding: 0; }
  html, body { width: 1200px; height: 900px; overflow: hidden; }
  body { background: var(--backdrop); position: relative; }

  .card {
    position: absolute;
    left: 240px;
    width: 720px;
    height: 400px;
    background: var(--card);
    box-shadow: 0 10px 30px rgba(0,0,0,.45);
  }
  .card--front { top: 40px; }
  .card--back  { top: 460px; }

  /* Front */
  .brand-name {
    position: absolute;
    top: 140px; left: 0; right: 0;
    text-align: center;
    font-family: "Josefin Sans", sans-serif;
    font-weight: 300;
    font-size: 46px;
    letter-spacing: 10px;
    color: var(--ink);
    text-transform: uppercase;
  }
  .brand-web {
    position: absolute;
    top: 262px; left: 0; right: 0;
    text-align: center;
    font-family: "Roboto", sans-serif;
    font-size: 16px;
    letter-spacing: 15px;
    color: var(--ink);
  }

  /* Back */
  .identity {
    position: absolute;
    top: 150px;
    right: 390px;
    text-align: right;
    font-family: "Roboto Condensed", sans-serif;
    text-transform: uppercase;
  }
  .identity__name { font-weight: 700; font-size: 26px; color: var(--accent); letter-spacing: .5px; }
  .identity__title { font-weight: 400; font-size: 20px; color: var(--ink); margin-top: 4px; letter-spacing: .5px; }

  .divider {
    position: absolute;
    left: 350px; top: 140px;
    width: 1px; height: 116px;
    background: var(--rule);
  }

  .contacts {
    position: absolute;
    left: 374px; top: 142px;
    list-style: none;
    font-family: "Roboto", sans-serif;
    font-size: 17px;
    color: var(--ink);
  }
  .contacts li { display: flex; align-items: center; height: 27px; }
  .contacts svg { width: 16px; height: 16px; margin-right: 10px; fill: var(--accent); flex: none; }

  .address {
    position: absolute;
    left: 110px; top: 308px;
    display: flex; align-items: center;
    font-family: "Roboto", sans-serif;
    font-size: 17px;
    color: var(--ink);
  }
  .address svg { width: 14px; height: 20px; margin-right: 8px; fill: var(--accent); }
</style>
</head>
<body>
  <section class="card card--front">
    <div class="brand-name">Corvane Holdings</div>
    <div class="brand-web">www.corvane.ae</div>
  </section>

  <section class="card card--back">
    <div class="identity">
      <div class="identity__name">Khalid Bin Tarrafi</div>
      <div class="identity__title">Managing Director</div>
    </div>
    <div class="divider"></div>
    <ul class="contacts">
      <li>
        <svg viewBox="0 0 24 24" aria-hidden="true"><path d="M6.6 10.8a15.1 15.1 0 0 0 6.6 6.6l2.2-2.2c.3-.3.7-.4 1-.2 1.1.4 2.3.6 3.6.6.6 0 1 .4 1 1V20c0 .6-.4 1-1 1C10.6 21 3 13.4 3 4c0-.6.4-1 1-1h3.5c.6 0 1 .4 1 1 0 1.3.2 2.5.6 3.6.1.3 0 .7-.2 1z"/></svg>
        +971 4 387 2940
      </li>
      <li>
        <svg viewBox="0 0 24 24" aria-hidden="true"><path d="M7 1h10a2 2 0 0 1 2 2v18a2 2 0 0 1-2 2H7a2 2 0 0 1-2-2V3a2 2 0 0 1 2-2zm0 3v14h10V4zm5 15.5a1 1 0 1 0 0 2 1 1 0 0 0 0-2z"/></svg>
        +971 50 518 2403
      </li>
      <li>
        <svg viewBox="0 0 24 24" aria-hidden="true"><path d="M2 5h20v14H2zm2 2v.5l8 5 8-5V7zm0 2.8V17h16V9.8l-8 5z"/></svg>
        khalid@corvane.ae
      </li>
      <li>
        <svg viewBox="0 0 24 24" aria-hidden="true"><path d="M12 2a10 10 0 1 0 0 20 10 10 0 0 0 0-20zm-1 17.9A8 8 0 0 1 4.2 10.6L9 15.4v1a2 2 0 0 0 2 2zm6.9-2.5a2 2 0 0 0-1.9-1.4h-1v-3a1 1 0 0 0-1-1H8v-2h2a1 1 0 0 0 1-1V7h2a2 2 0 0 0 2-2v-.4a8 8 0 0 1 2.9 12.8z"/></svg>
        www.corvane.ae
      </li>
    </ul>
    <div class="address">
      <svg viewBox="0 0 24 34" aria-hidden="true"><path d="M12 0C5.4 0 0 5.4 0 12c0 9 12 22 12 22s12-13 12-22C24 5.4 18.6 0 12 0zm0 17a5 5 0 1 1 0-10 5 5 0 0 1 0 10z"/></svg>
      Q-Span Plaza, officw 18-B07, Warqa Gardens, Dubai
    </div>
  </section>
</body>
</html>
```